We're launching a new live touring show called "Thoughtcatchers, Seers and Reason - A LIVE THEATRE JOURNEY" and we're looking to create a show poster. The itself will be a combination of mentalism tricks that are explainable done by one expert/magician and another expert who is well studied in the science of mind reading, telepathy, telekinesis, etc. The audience will be left entertained and learning that there are some things in science that are still yet to be explained. We'd like the poster to have it clear that it's a live show with 2 experts (man and a woman) and we want it to feel like a mix of academic and entertainment value. Not too mystical. No crystal balls or anything.

```html
<!DOCTYPE html>
<html lang="en">
<head>
<meta charset="utf-8">
<title>Thoughtcatchers, Seers and Reason – A Live Theatre Journey</title>
<link rel="stylesheet" href="https://fonts.googleapis.com/css2?family=Antonio:wght@400;500&family=Montserrat:wght@700&display=swap">
<style>
  :root {
    --stage-deep: #0d1118;
    --stage-mid: #1f2835;
    --stage-glow: #5d6878;
    --title-white: #ffffff;
    --title-gold: #e2b866;
    --bar-black: #0e0e0e;
  }
  html, body {
    margin: 0;
    padding: 0;
    width: 1200px;
    height: 1200px;
    overflow: hidden;
    background: var(--stage-deep);
  }
  .poster {
    position: relative;
    width: 1200px;
    height: 1200px;
    overflow: hidden;
    background:
      radial-gradient(ellipse 620px 420px at 50% 82%, var(--stage-glow) 0%, rgba(93,104,120,0) 70%),
      radial-gradient(ellipse 900px 700px at 50% 55%, var(--stage-mid) 0%, var(--stage-deep) 80%);
  }
  .stage-lights, .title {
    position: absolute;
    inset: 0;
  }
  .title-main {
    font-family: "Antonio", "Arial Narrow", sans-serif;
    font-weight: 500;
    fill: var(--title-white);
  }
  .title-reason {
    font-family: "Montserrat", Arial, sans-serif;
    font-weight: 700;
    fill: var(--title-white);
  }
  .title-tagline {
    font-family: "Antonio", "Arial Narrow", sans-serif;
    font-weight: 400;
    fill: var(--title-gold);
  }
  .mind-illustration {
    position: absolute;
    left: 368px;
    top: 484px;
    width: 420px;
    height: 524px;
    border-radius: 48% 48% 30% 36% / 40% 40% 24% 24%;
    background:
      radial-gradient(circle at 57% 52%, rgba(255,255,255,0.95) 0%, rgba(255,255,255,0) 10%),
      linear-gradient(90deg, rgba(63,182,255,0.55) 0%, rgba(63,182,255,0.55) 55%, rgba(255,74,99,0.55) 58%, rgba(255,74,99,0.5) 100%),
      linear-gradient(180deg, rgba(190,200,215,0.5) 0%, rgba(120,130,150,0.15) 100%);
    box-shadow: 0 0 40px rgba(180,200,230,0.25);
  }
  .info-bar {
    position: absolute;
    left: 286px;
    top: 1078px;
    width: 662px;
    height: 71px;
    border-radius: 22px;
    background: var(--bar-black);
  }
  .info-bar svg {
    display: block;
  }
  .experts-line {
    font-family: "Antonio", "Arial Narrow", sans-serif;
    font-weight: 400;
    fill: var(--title-gold);
  }
</style>
</head>
<body>
<main class="poster">
  <svg class="stage-lights" width="1200" height="1200" viewBox="0 0 1200 1200" aria-hidden="true">
    <defs>
      <linearGradient id="beamFade" x1="0" y1="0" x2="0" y2="1">
        <stop offset="0" stop-color="#d6e2f2" stop-opacity="0.22"/>
        <stop offset="1" stop-color="#d6e2f2" stop-opacity="0"/>
      </linearGradient>
      <filter id="soften" x="-20%" y="-20%" width="140%" height="140%">
        <feGaussianBlur stdDeviation="18"/>
      </filter>
    </defs>
    <polygon points="28,112 58,112 330,900 -120,900" fill="url(#beamFade)" filter="url(#soften)"/>
    <polygon points="1135,112 1165,112 1320,900 870,900" fill="url(#beamFade)" filter="url(#soften)"/>
    <ellipse cx="40" cy="112" rx="22" ry="12" fill="#f4f6f8" transform="rotate(-20 40 112)"/>
    <ellipse cx="1150" cy="112" rx="22" ry="12" fill="#f4f6f8" transform="rotate(20 1150 112)"/>
    <line x1="0" y1="496" x2="1200" y2="496" stroke="#8a96a8" stroke-opacity="0.25" stroke-width="2"/>
    <line x1="0" y1="1040" x2="1200" y2="1040" stroke="#a9b3c2" stroke-opacity="0.35" stroke-width="2"/>
    <line x1="160" y1="1040" x2="290" y2="960" stroke="#a9b3c2" stroke-opacity="0.2" stroke-width="2"/>
    <line x1="1040" y1="1040" x2="910" y2="960" stroke="#a9b3c2" stroke-opacity="0.2" stroke-width="2"/>
  </svg>

  <div class="mind-illustration" role="img" aria-label="Glowing side-profile head with a brain drawn as circuitry, blue on one half and red on the other"></div>

  <svg class="title" width="1200" height="1200" viewBox="0 0 1200 1200" role="heading" aria-level="1" aria-label="Thoughtcatchers &amp; Seers and Reason – A Live Theatre Journey">
    <text class="title-main" x="596" y="160" text-anchor="middle" font-size="104" textLength="909" lengthAdjust="spacingAndGlyphs">THOUGHTCATCHERS &amp; SEERS</text>
    <text class="title-reason" x="593" y="278" text-anchor="middle" font-size="80" textLength="541" lengthAdjust="spacingAndGlyphs">AND REASON</text>
    <text class="title-tagline" x="596" y="391" text-anchor="middle" font-size="72" textLength="988" lengthAdjust="spacing">A LIVE THEATRE JOURNEY</text>
  </svg>

  <div class="info-bar">
    <svg width="662" height="71" viewBox="0 0 662 71">
      <text class="experts-line" x="331" y="46" text-anchor="middle" font-size="28" textLength="600" lengthAdjust="spacing">HE PERFORMS THE IMPOSSIBLE · SHE EXPLAINS THE SCIENCE</text>
    </svg>
  </div>
</main>
</body>
</html>
```